Business Card Design

WE are looking for a premium quality Business Cards for a Law Firm . Copies of our current business card is attached.

Contact Information for Business Card

xyz

```html
<!DOCTYPE html>
<html lang="en">
<head>
<meta charset="utf-8">
<title>Ashgrove Lawyers – Business Card</title>
<link href="https://fonts.googleapis.com/css2?family=Montserrat:wght@400;500;600;700&display=swap" rel="stylesheet">
<style>
  :root {
    --green: #0f2a1e;
    --green-deep: #0a2117;
    --gold: #bf9b55;
    --ink: #1e1e1e;
    --paper: #ffffff;
    --backdrop: #e6e6e6;
    --rule: #9a9a9a;
  }
  * { box-sizing: border-box; margin: 0; padding: 0; }
  html, body { width: 1200px; height: 1200px; overflow: hidden; }
  body {
    background: var(--backdrop);
    font-family: "Montserrat", Arial, sans-serif;
    color: var(--ink);
    position: relative;
  }
  .card {
    position: absolute;
    left: 160px;
    width: 880px;
    height: 500px;
    background: var(--paper);
    border-radius: 34px;
    overflow: hidden;
    box-shadow: 0 10px 30px rgba(0,0,0,0.15);
  }
  .card--front { top: 70px; }
  .card--back { top: 630px; }
  .card__shapes { position: absolute; inset: 0; }

  /* front */
  .person { position: absolute; left: 64px; top: 120px; }
  .person__name {
    color: var(--gold);
    font-weight: 700;
    font-size: 40px;
    letter-spacing: 1px;
    line-height: 1;
  }
  .person__title {
    margin-top: 10px;
    font-size: 14px;
    font-weight: 500;
    line-height: 1.25;
    letter-spacing: 0.3px;
    text-transform: uppercase;
  }
  .contacts { list-style: none; margin-top: 22px; }
  .contacts li {
    display: flex;
    align-items: center;
    gap: 12px;
    font-size: 17px;
    height: 36px;
  }
  .contacts .icon {
    width: 26px; height: 26px;
    border-radius: 50%;
    background: var(--gold);
    display: flex; align-items: center; justify-content: center;
    flex: none;
  }
  .divider {
    position: absolute;
    left: 450px; top: 110px;
    width: 1px; height: 220px;
    background: var(--rule);
  }
  .brand {
    position: absolute;
    display: flex;
    flex-direction: column;
    align-items: center;
    color: var(--green);
    font-weight: 600;
    text-align: center;
  }
  .brand__mark {
    width: 64px; height: 64px;
    border-radius: 50%;
    border: 4px solid var(--gold);
    margin-bottom: 14px;
  }
  .brand__name { line-height: 1.15; }
  .brand__main { display: block; font-size: 46px; letter-spacing: 2px; }
  .brand__sub { display: block; font-size: 18px; letter-spacing: 12px; padding-left: 12px; }
  .brand--front { left: 490px; top: 96px; width: 340px; }
  .brand--back { left: 430px; top: 40px; width: 360px; }
  .address {
    position: absolute;
    right: 60px; top: 332px;
    text-align: right;
    font-size: 21px;
    line-height: 1.35;
  }

  /* back */
  .office {
    position: absolute;
    color: var(--paper);
    font-size: 15px;
    line-height: 1.4;
  }
  .office__label {
    color: var(--gold);
    font-weight: 600;
    font-size: 16px;
    text-transform: uppercase;
    margin-bottom: 4px;
  }
  .office__row { display: flex; gap: 10px; align-items: flex-start; }
  .office__row svg { flex: none; margin-top: 2px; }
  .office--brisbane { left: 60px; top: 372px; width: 360px; }
  .office--melbourne { left: 500px; top: 300px; width: 340px; }
  .office-divider {
    position: absolute;
    left: 470px; top: 318px;
    width: 1px; height: 130px;
    background: rgba(255,255,255,0.35);
  }
</style>
</head>
<body>

<section class="card card--front" aria-label="Business card front">
  <svg class="card__shapes" width="880" height="500" viewBox="0 0 880 500">
    <polygon points="0,474 560,474 550,500 0,500" fill="var(--gold)"/>
    <polygon points="580,500 596,436 880,436 880,500" fill="var(--green)"/>
  </svg>

  <div class="person">
    <h1 class="person__name">DANIEL HARTLEY</h1>
    <p class="person__title">Director &amp; Principal Solicitor<br>MBA, Juris Doctor</p>
    <ul class="contacts">
      <li><span class="icon"><svg width="14" height="14" viewBox="0 0 24 24"><path fill="#fff" d="M6.6 10.8a15 15 0 0 0 6.6 6.6l2.2-2.2c.3-.3.7-.4 1-.2 1.1.4 2.3.6 3.6.6.6 0 1 .4 1 1V20c0 .6-.4 1-1 1A17 17 0 0 1 3 4c0-.6.4-1 1-1h3.5c.6 0 1 .4 1 1 0 1.3.2 2.5.6 3.6.1.3 0 .7-.2 1z"/></svg></span>+61 7 3555 0142</li>
      <li><span class="icon"><svg width="12" height="14" viewBox="0 0 16 24"><rect x="2" y="1" width="12" height="22" rx="2" fill="none" stroke="#fff" stroke-width="2"/><circle cx="8" cy="19" r="1.3" fill="#fff"/></svg></span>+61 0400 555 318</li>
      <li><span class="icon"><svg width="14" height="12" viewBox="0 0 24 18"><rect x="1" y="1" width="22" height="16" rx="1" fill="none" stroke="#fff" stroke-width="2"/><path d="M1 2l11 8 11-8" fill="none" stroke="#fff" stroke-width="2"/></svg></span>daniel@ashgrovelawyers.com.au</li>
      <li><span class="icon"><svg width="14" height="14" viewBox="0 0 24 24" fill="none" stroke="#fff" stroke-width="1.8"><circle cx="12" cy="12" r="10"/><ellipse cx="12" cy="12" rx="4.5" ry="10"/><path d="M2 12h20M4 7h16M4 17h16"/></svg></span>www.ashgrovelawyers.com.au</li>
    </ul>
  </div>

  <div class="divider"></div>

  <div class="brand brand--front">
    <span class="brand__mark"></span>
    <p class="brand__name"><span class="brand__main">ASHGROVE</span><span class="brand__sub">LAWYERS</span></p>
  </div>

  <p class="address">Level 3, Ashgrove House,<br>212 Corbett Terrace, Spring Hill, QLD 4000</p>
</section>

<section class="card card--back" aria-label="Business card back">
  <svg class="card__shapes" width="880" height="500" viewBox="0 0 880 500">
    <line x1="0" y1="322" x2="880" y2="212" stroke="var(--gold)" stroke-width="6"/>
    <polygon points="0,338 880,228 880,500 0,500" fill="var(--green-deep)"/>
  </svg>

  <div class="brand brand--back">
    <span class="brand__mark"></span>
    <p class="brand__name"><span class="brand__main">ASHGROVE</span><span class="brand__sub">LAWYERS</span></p>
  </div>

  <div class="office office--brisbane">
    <p class="office__label">Brisbane Office</p>
    <div class="office__row">
      <svg width="14" height="18" viewBox="0 0 24 32"><path fill="var(--gold)" d="M12 0a11 11 0 0 0-11 11c0 8 11 21 11 21s11-13 11-21A11 11 0 0 0 12 0zm0 16a5 5 0 1 1 0-10 5 5 0 0 1 0 10z"/></svg>
      <p>Level 3, Ashgrove House, 212 Corbett Terrace Spring Hill QLD 4000</p>
    </div>
    <div class="office__row">
      <svg width="16" height="16" viewBox="0 0 24 24"><path fill="var(--gold)" d="M6.6 10.8a15 15 0 0 0 6.6 6.6l2.2-2.2c.3-.3.7-.4 1-.2 1.1.4 2.3.6 3.6.6.6 0 1 .4 1 1V20c0 .6-.4 1-1 1A17 17 0 0 1 3 4c0-.6.4-1 1-1h3.5c.6 0 1 .4 1 1 0 1.3.2 2.5.6 3.6.1.3 0 .7-.2 1z"/></svg>
      <p>(07) 3555 0142</p>
    </div>
  </div>

  <div class="office-divider"></div>

  <div class="office office--melbourne">
    <p class="office__label">Melbourne Office</p>
    <div class="office__row">
      <svg width="14" height="18" viewBox="0 0 24 32"><path fill="var(--gold)" d="M12 0a11 11 0 0 0-11 11c0 8 11 21 11 21s11-13 11-21A11 11 0 0 0 12 0zm0 16a5 5 0 1 1 0-10 5 5 0 0 1 0 10z"/></svg>
      <p>Suite 205, Harcourt Chambers, 418 Little Bourke Street, Melbourne, VIC, 3000</p>
    </div>
    <div class="office__row">
      <svg width="16" height="16" viewBox="0 0 24 24"><path fill="var(--gold)" d="M6.6 10.8a15 15 0 0 0 6.6 6.6l2.2-2.2c.3-.3.7-.4 1-.2 1.1.4 2.3.6 3.6.6.6 0 1 .4 1 1V20c0 .6-.4 1-1 1A17 17 0 0 1 3 4c0-.6.4-1 1-1h3.5c.6 0 1 .4 1 1 0 1.3.2 2.5.6 3.6.1.3 0 .7-.2 1z"/></svg>
      <p>(07) 3555 0142</p>
    </div>
  </div>
</section>

</body>
</html>
```